Quiet Braising For The Patient Epicure

Hi, I had a book cover designed on this site, but I want to modify the cover and change the colours. I want to keep the slow cooker and the ingredients on the cover, but I want to simplify it a bit. And, I am open to other ideas. I have attached below a book cover idea I like and I like the colors as well. I want it to be called Quiet Braising, with the language on the right corner: "Curated For Nearly Effortless Meals That Are Greater Than The Sum Of Their Ingredients" I like the circles idea and my name as the author on the curve.

Target Market(s)

Home Cooks

Colors
00AB8E
00BBA5
67D7C9
C6EFE9
E9F9F6
F0912C
F2A743
F7CA91
FBE8D2
FDF5EE
E54698
E96AAD
F1A4CE
F9D9EA
FCEFF6
6B429C
8869AF
B7A5CE
E3DAEB
F3F0F8

Requirements
Must have
• Please use the colors on the Harvest Table Cook Book and I like the design, but I do not want it identical. I like the author name (Marcus T. Hallbright) on the side of the circle on the upper right side of the cover.
Nice to have
• I like the large words "Quiet Braising"

```html
<!DOCTYPE html>
<html lang="en">
<head>
<meta charset="utf-8">
<title>Quiet Braising – Book Cover</title>
<link href="https://fonts.googleapis.com/css2?family=Playfair+Display:wght@400&family=Tinos&family=Oswald:wght@500&display=swap" rel="stylesheet">
<style>
  :root {
    --stage: #262626;
    --paper: #ffffff;
    --ink: #1a1a1a;
    --tagline-ink: #3a3a3a;
    --white: #ffffff;
    --orange: #f0912c;
    --amber: #f2a743;
    --red: #e2351f;
    --maroon: #5a1238;
    --gold: #f2d468;
    --night: #140a14;
  }
  * { margin: 0; padding: 0; box-sizing: border-box; }
  html, body { width: 1200px; height: 1200px; overflow: hidden; background: var(--stage); }
  .stage { position: relative; width: 1200px; height: 1200px; background: var(--stage); }

  /* Back cover */
  .back-cover {
    position: absolute; left: 35px; top: 182px; width: 556px; height: 835px;
    background: var(--paper);
  }
  .back-title {
    position: absolute; left: 40px; top: 44px;
    display: inline-block;
    padding: 10px 8px 34px 0;
    font-family: "Playfair Display", serif; font-weight: 400;
    font-size: 76px; line-height: 52px; letter-spacing: -3px;
    background: linear-gradient(100deg, var(--maroon) 0%, var(--orange) 18%, var(--amber) 40%, var(--red) 70%, var(--maroon) 100%);
    -webkit-background-clip: text; background-clip: text; color: transparent;
  }
  .back-title .line-one { display: block; padding-left: 42px; }
  .back-title .line-two { display: block; }
  .back-tagline {
    position: absolute; right: 40px; top: 81px; width: 200px;
    font-family: "Playfair Display", serif; font-size: 16.5px; line-height: 21px;
    color: var(--tagline-ink); text-align: right; white-space: nowrap;
  }
  .back-blurb {
    position: absolute; left: 38px; top: 199px; width: 482px;
    font-family: "Tinos", serif; font-size: 15.5px; line-height: 19.4px;
    color: var(--ink); text-align: center;
  }
  .back-blurb p + p { margin-top: 19.4px; }

  /* Front cover */
  .front-cover {
    position: absolute; left: 609px; top: 182px; width: 556px; height: 835px;
    overflow: hidden; background: var(--night);
  }
  .cover-art { position: absolute; inset: 0; }
  .author-arc { position: absolute; left: 0; top: 0; }
  .author-arc text { font-family: "Playfair Display", serif; font-size: 23px; fill: var(--white); letter-spacing: 1px; }
  .front-title {
    position: absolute; left: 38px; top: 196px;
    font-family: "Playfair Display", serif; font-weight: 400;
    font-size: 106px; line-height: 72px; letter-spacing: -4px; color: var(--white);
  }
  .front-title .line-one { display: block; padding-left: 58px; }
  .front-title .line-two { display: block; }
  .front-tagline {
    position: absolute; right: 34px; top: 551px; width: 240px;
    font-family: "Playfair Display", serif; font-size: 18px; line-height: 23px;
    color: var(--white); text-align: right; white-space: nowrap;
  }
  .pairing-badge { position: absolute; left: 30px; top: 530px; }
  .pairing-badge text { font-family: "Oswald", sans-serif; font-weight: 500; fill: #111; text-anchor: middle; }
  .kitchen-scene { position: absolute; left: 0; top: 660px; width: 556px; height: 175px; }
</style>
</head>
<body>
<div class="stage">

  <section class="back-cover">
    <h2 class="back-title"><span class="line-one">Quiet</span><span class="line-two">Braising</span></h2>
    <p class="back-tagline">Curated For Nearly<br>Effortless Meals That Are<br>Greater Than The Sum Of<br>Their Ingredients</p>
    <div class="back-blurb">
      <p>Lorem ipsum dolor sit amet, consectetur adipiscing elit, sed do eiusmod tempor incididunt ut labore et dolore magna aliqua. Quis ipsum suspendisse ultrices gravida. Risus commodo viverra maecenas accumsan lacus vel facilisis. Lorem ipsum dolor sit amet, consectetur adipiscing elit, sed do eiusmod tempor incididunt ut labore et dolore magna aliqua. Quis ipsum suspendisse ultrices gravida. Risus commodo viverra maecenas accumsan lacus vel facilisis. Lorem ipsum dolor sit amet, consectetur adipiscing elit, sed do eiusmod tempor incididunt ut labore et dolore magna aliqua. Quis ipsum suspendisse ultrices gravida. Risus commodo viverra maecenas accumsan lacus vel facilisis. Lorem ipsum dolor sit amet, consectetur adipiscing elit, sed do eiusmod tempor incididunt ut labore et dolore magna aliqua. Quis ipsum suspendisse ultrices gravida. Risus commodo viverra maecenas accumsan lacus vel facilisis. Lorem ipsum dolor sit amet, consectetur adipiscing elit, sed do eiusmod tempor incididunt ut labore et dolore magna aliqua. Quis ipsum suspendisse ultrices gravida. Risus commodo viverra maecenas accumsan lacus vel facilisis.</p>
      <p>Lorem ipsum dolor sit amet, consectetur adipiscing elit, sed do eiusmod tempor incididunt ut labore et dolore magna aliqua. Quis ipsum suspendisse ultrices gravida. Risus commodo viverra maecenas accumsan lacus vel facilisis. Lorem ipsum dolor sit amet, consectetur adipiscing elit, sed do eiusmod tempor incididunt ut labore et dolore magna aliqua. Quis ipsum suspendisse ultrices gravida. Risus commodo viverra maecenas accumsan lacus vel facilisis.</p>
    </div>
  </section>

  <section class="front-cover">
    <svg class="cover-art" width="556" height="835" viewBox="0 0 556 835" role="img" aria-label="Watercolour illustration of overlapping translucent circles in blue, orange, red and magenta with a faint clock face">
      <defs>
        <radialGradient id="glow-blue" cx="0.25" cy="0.12" r="0.45">
          <stop offset="0" stop-color="#2f7fa0"/><stop offset="1" stop-color="#2f7fa0" stop-opacity="0"/>
        </radialGradient>
        <radialGradient id="glow-orange" cx="0.4" cy="0.5" r="0.42">
          <stop offset="0" stop-color="#ff8a1a"/><stop offset="1" stop-color="#ff8a1a" stop-opacity="0"/>
        </radialGradient>
        <radialGradient id="glow-red" cx="0.88" cy="0.42" r="0.38">
          <stop offset="0" stop-color="#f0203a"/><stop offset="1" stop-color="#f0203a" stop-opacity="0"/>
        </radialGradient>
        <radialGradient id="glow-magenta" cx="0.6" cy="0.75" r="0.45">
          <stop offset="0" stop-color="#c8268c"/><stop offset="1" stop-color="#c8268c" stop-opacity="0"/>
        </radialGradient>
        <radialGradient id="glow-amber" cx="0.85" cy="0.08" r="0.35">
          <stop offset="0" stop-color="#d8781a"/><stop offset="1" stop-color="#d8781a" stop-opacity="0"/>
        </radialGradient>
      </defs>
      <rect width="556" height="835" fill="#2a1518"/>
      <rect width="556" height="835" fill="url(#glow-amber)"/>
      <rect width="556" height="835" fill="url(#glow-blue)"/>
      <rect width="556" height="835" fill="url(#glow-red)"/>
      <rect width="556" height="835" fill="url(#glow-magenta)"/>
      <rect width="556" height="835" fill="url(#glow-orange)"/>
    </svg>

    <svg class="author-arc" width="556" height="300" viewBox="0 0 556 300">
      <path id="author-curve" d="M 100 160 Q 200 60 310 115" fill="none"/>
      <text><textPath href="#author-curve">Marcus T. Hallbright</textPath></text>
    </svg>

    <h1 class="front-title"><span class="line-one">Quiet</span><span class="line-two">Braising</span></h1>

    <svg class="pairing-badge" width="140" height="140" viewBox="-70 -70 140 140">
      <g transform="rotate(-6)">
        <polygon fill="var(--gold)" points="0,-66 8,-55 19,-63 23,-50 36,-55 35,-42 49,-44 44,-31 58,-29 49,-18 62,-12 51,-4 62,6 50,12 59,23 45,26 51,40 37,39 39,53 26,49 23,63 12,55 4,66 -4,55 -14,64 -18,51 -30,58 -31,44 -45,47 -41,34 -55,32 -47,21 -61,16 -50,7 -62,-2 -51,-9 -60,-20 -46,-24 -52,-37 -38,-38 -40,-52 -27,-48 -22,-61 -12,-53"/>
        <text y="-23" font-size="18">WITH</text>
        <text y="-4" font-size="13.5" transform="scale(0.85,1)">RECOMMENDED</text>
        <text y="19" font-size="22">WINE</text>
        <text y="40" font-size="21" transform="scale(0.9,1)">PAIRINGS</text>
      </g>
    </svg>

    <p class="front-tagline">Curated For Nearly<br>Effortless Meals That Are<br>Greater Than The Sum Of<br>Their Ingredients</p>

    <svg class="kitchen-scene" width="556" height="175" viewBox="0 0 556 175" role="img" aria-label="Wooden kitchen table with a red slow cooker, copper pot, bread, wine bottles, fresh vegetables, fish, cheese and roast chicken">
      <defs>
        <linearGradient id="table-tones" x1="0" y1="0" x2="0" y2="1">
          <stop offset="0" stop-color="#140a14" stop-opacity="0"/>
          <stop offset="0.35" stop-color="#7a3a22"/>
          <stop offset="0.72" stop-color="#8a5a34"/>
          <stop offset="0.74" stop-color="#d8c7a8"/>
          <stop offset="1" stop-color="#e3d6bd"/>
        </linearGradient>
      </defs>
      <rect width="556" height="175" fill="url(#table-tones)"/>
    </svg>
  </section>

</div>
</body>
</html>
```